Business Card Design For Marketing Agnecy LVP

Need business card design for marketing agency.

Doug Fenwick
President, CEO
1-555-302-4196
doug@boldpromoperksgroup.example
www.BoldPromoPerksGroup.example

Back Side:
Boost Sales Using Rewards, Incentives & Giveaways
Get A Free Sample Package

Target Market(s)

B2B

Industry/Entity Type

Marketing

Contact Information for Business Card

Doug Fenwick
President, CEO
1-555-302-4196

Back Side:
Get A Free Sample Package

Please note that my current url is OLD DESIGN. I am working on new design and want the business card to match color themes at least on new site. Here is the demo link for new site so you can see the colors I use, etc.

http://layoutcratehub.example/kq/doug/lvp_final/index.html

Requirements
Must have
• Please note that my current url is OLD DESIGN. I am working on new design and want the business card to match color themes at least on new site. Here is the demo link for new site so you can see the colors I use, etc.

Nice to have

Should not have

```html
<!DOCTYPE html>
<html lang="en">
<head>
<meta charset="utf-8">
<title>LVP Business Card</title>
<link rel="stylesheet" href="https://fonts.googleapis.com/css2?family=Montserrat:wght@600;700;800&family=Roboto+Condensed:wght@400;500&display=swap">
<style>
  :root {
    --backdrop: #3b3b3d;
    --card: #1f2022;
    --card-edge: #2a2b2e;
    --brand-blue: #2f67b8;
    --brand-green: #52b432;
    --ink-light: #f2f2f2;
    --ink-muted: #8a8c90;
    --front-mark: #6f7276;
  }
  * { box-sizing: border-box; margin: 0; padding: 0; }
  html, body {
    width: 799px; height: 1200px; overflow: hidden;
    background: var(--backdrop);
  }
  .canvas {
    position: relative; width: 799px; height: 1200px;
    display: flex; flex-direction: column; align-items: center;
    justify-content: space-around; padding: 60px 0;
  }
  .card {
    position: relative; width: 630px; height: 360px;
    background: var(--card);
    border: 1px solid var(--card-edge);
    box-shadow: 0 14px 30px rgba(0,0,0,.45);
    overflow: hidden;
  }
  /* Front */
  .card--front { display: flex; align-items: center; justify-content: center; }
  .brand-name {
    font-family: "Montserrat", sans-serif; font-weight: 800;
    text-align: center; line-height: 1;
    text-transform: uppercase;
  }
  .brand-name__short { display: block; font-size: 110px; letter-spacing: 4px; }
  .brand-name__long { display: block; font-size: 24px; letter-spacing: 3px; margin-top: 14px; }
  .card--front .brand-name { color: var(--front-mark); }

  /* Back */
  .holder {
    position: absolute; left: 34px; top: 36px;
  }
  .holder__name {
    font-family: "Montserrat", sans-serif; font-weight: 600;
    font-size: 24px; color: var(--brand-blue);
  }
  .holder__title {
    font-family: "Roboto Condensed", sans-serif; font-size: 15px;
    color: var(--ink-light); margin-top: 4px;
  }
  .contacts {
    position: absolute; left: 34px; top: 196px; list-style: none;
    font-family: "Roboto Condensed", sans-serif; font-size: 15px;
    color: var(--ink-light);
  }
  .contacts li { display: flex; align-items: center; gap: 10px; height: 22px; }
  .contacts svg { width: 13px; height: 13px; fill: var(--brand-blue); flex: none; }
  .card--back .brand-name {
    position: absolute; right: 40px; top: 170px; color: var(--brand-blue);
  }
  .card--back .brand-name__short { font-size: 76px; letter-spacing: 3px; }
  .card--back .brand-name__long { font-size: 16px; letter-spacing: 2px; margin-top: 8px; }
  .accent-line {
    position: absolute; left: 0; bottom: 46px; width: 50%; height: 10px;
    background: var(--brand-green);
  }
  .offer-tab {
    position: absolute; right: 0; bottom: 0; width: 50%; height: 56px;
    background: var(--brand-blue); border-top-left-radius: 16px;
    display: flex; align-items: center; justify-content: center;
    font-family: "Montserrat", sans-serif; font-weight: 700;
    font-size: 18px; color: var(--ink-light);
  }
</style>
</head>
<body>
<main class="canvas">
  <section class="card card--front" aria-label="Card front">
    <p class="brand-name">
      <span class="brand-name__short">LVP</span>
      <span class="brand-name__long">Bold Promo Perks Group</span>
    </p>
  </section>

  <section class="card card--back" aria-label="Card back">
    <div class="holder">
      <h1 class="holder__name">Doug Fenwick</h1>
      <p class="holder__title">President, CEO</p>
    </div>
    <ul class="contacts">
      <li>
        <svg viewBox="0 0 24 24" aria-hidden="true"><path d="M6.6 10.8a15.1 15.1 0 0 0 6.6 6.6l2.2-2.2a1 1 0 0 1 1-.25 11.4 11.4 0 0 0 3.6.57 1 1 0 0 1 1 1V20a1 1 0 0 1-1 1A17 17 0 0 1 3 4a1 1 0 0 1 1-1h3.5a1 1 0 0 1 1 1c0 1.25.2 2.45.57 3.57a1 1 0 0 1-.25 1z"/></svg>
        1-555-302-4196
      </li>
      <li>
        <svg viewBox="0 0 24 24" aria-hidden="true"><path d="M2 5h20v14H2z M3.5 6.5 12 13l8.5-6.5" fill-rule="evenodd"/></svg>
        doug@boldpromoperksgroup.example
      </li>
      <li>
        <svg viewBox="0 0 24 24" aria-hidden="true"><circle cx="12" cy="12" r="10"/></svg>
        www.BoldPromoPerksGroup.example
      </li>
    </ul>
    <p class="brand-name">
      <span class="brand-name__short">LVP</span>
      <span class="brand-name__long">Bold Promo Perks Group</span>
    </p>
    <div class="accent-line"></div>
    <div class="offer-tab">Get A Free Sample Package</div>
  </section>
</main>
</body>
</html>
```